Velmora Consulting Business

** Please add the content information from my old business card
1. I would like to see a two sided business card with both options with the 1st Option--Tallow Spire-new WHITE BACKGROUND LOGO
2 nd Option-Tallow Spire - new BLACK- Background Logo
3rd -Option a business card with my Photo on the card
Please add the new word to the card information:
EXECUTION
AS THE OWNER'S REP
WE AIM TO ACHIEVE YOUR
INFRASTRUCTURE VISION with
OUR SPECIALIZATION & EXECUTION in:

FUNDING Planning
BUSINESS Planning
INFRASTRUCTURE Planning
PROJECT Management
Since 2012
_____________________________________________________________________
I want to get spot uv raised printing. I was liking a a nice rich white linen paper stock with black writing & NOT A COLORED CARD other than a variety of white or black cards concept

```html
<!DOCTYPE html>
<html lang="en">
<head>
<meta charset="utf-8">
<title>Velmora Consulting – Business Card</title>
<link href="https://fonts.googleapis.com/css2?family=Source+Sans+3:wght@400;600;700&display=swap" rel="stylesheet">
<style>
  :root {
    --backdrop: #2b2b2d;
    --card-white: #ffffff;
    --card-black: #1c1c1e;
    --ink: #1a1a1a;
    --accent-red: #e5173f;
    --rule-grey: #8a8a8a;
    --reverse-text: #f2f2f2;
  }
  * { margin: 0; padding: 0; box-sizing: border-box; }
  html, body {
    width: 1200px; height: 1108px; overflow: hidden;
    background: var(--backdrop);
    font-family: "Source Sans 3", "Myriad Pro", Arial, sans-serif;
  }
  .canvas {
    position: relative; width: 1200px; height: 1108px;
    display: flex; justify-content: center; align-items: center; gap: 60px;
  }
  .card {
    position: relative; width: 360px; height: 620px;
    border-radius: 22px; overflow: hidden;
    box-shadow: 0 18px 40px rgba(0,0,0,.55);
  }
  /* Front */
  .card-front {
    background: var(--card-white); color: var(--ink);
    display: flex; flex-direction: column; align-items: center;
    padding-top: 150px; text-align: center;
  }
  .brand { display: flex; align-items: center; gap: 10px; }
  .brand-name { font-size: 72px; font-weight: 700; letter-spacing: -1px; line-height: 1; }
  .brand-mark { width: 16px; height: 16px; background: var(--accent-red); }
  .brand-sub {
    margin-top: 10px; font-size: 17px; font-weight: 400;
    letter-spacing: 14px; padding-left: 14px;
  }
  .person-name { margin-top: 46px; font-size: 25px; font-weight: 700; }
  .person-title {
    margin-top: 4px; font-size: 16px; color: var(--accent-red);
    text-transform: uppercase; letter-spacing: .3px;
  }
  .icon-row {
    margin-top: 20px; width: 280px;
    display: flex; align-items: center; gap: 8px;
  }
  .icon-row .rule { flex: 1; height: 1px; background: var(--rule-grey); }
  .icon { width: 28px; height: 28px; border-radius: 5px; background: var(--accent-red); display: flex; align-items: center; justify-content: center; }
  .contact { margin-top: 14px; font-size: 21px; line-height: 1.32; }
  .divider { margin-top: 18px; width: 280px; height: 1px; background: var(--rule-grey); }
  .locations { margin-top: 14px; font-size: 20px; }
  .locations .dot { color: var(--accent-red); padding: 0 4px; }
  /* Back */
  .card-back {
    background: var(--card-black); color: var(--reverse-text);
    display: flex; flex-direction: column; align-items: center; text-align: center;
  }
  .back-pattern {
    position: absolute; inset: 0;
    background: radial-gradient(ellipse at 50% 40%, #26262a 0%, #18181a 80%);
  }
  .back-content { position: relative; display: flex; flex-direction: column; align-items: center; width: 100%; }
  .back-brand { margin-top: 170px; display: flex; align-items: center; gap: 6px; }
  .back-brand .brand-name { font-size: 34px; color: var(--reverse-text); }
  .back-brand .brand-mark { width: 9px; height: 9px; }
  .back-brand-sub { margin-top: 3px; font-size: 9px; letter-spacing: 6px; padding-left: 6px; }
  .mission {
    margin-top: 80px; font-size: 17px; line-height: 1.35;
    text-transform: uppercase; letter-spacing: .2px;
  }
  .services { margin-top: 22px; font-size: 17px; line-height: 1.35; }
  .since { margin-top: 18px; font-size: 17px; }
</style>
</head>
<body>
<main class="canvas">

  <section class="card card-front" aria-label="Card front">
    <div class="brand">
      <span class="brand-name">Velmora</span>
      <span class="brand-mark"></span>
    </div>
    <div class="brand-sub">CONSULTING</div>

    <h1 class="person-name">Marisol Dunleavy-Okafor</h1>
    <p class="person-title">CEO / Lead Project Manager</p>

    <div class="icon-row">
      <span class="rule"></span>
      <span class="icon" aria-label="Phone">
        <svg width="16" height="16" viewBox="0 0 16 16"><path d="M4 1.5l2 3-1.3 1.3a8 8 0 0 0 5.5 5.5L11.5 10l3 2-1 2.5C7 15 1 9 1.5 2.5z" fill="#fff"/></svg>
      </span>
      <span class="icon" aria-label="Email">
        <svg width="16" height="16" viewBox="0 0 16 16"><rect x="1.5" y="3.5" width="13" height="9" fill="none" stroke="#fff" stroke-width="1.4"/><path d="M1.5 3.5L8 9l6.5-5.5" fill="none" stroke="#fff" stroke-width="1.4"/></svg>
      </span>
      <span class="icon" aria-label="Website">
        <svg width="16" height="16" viewBox="0 0 16 16"><circle cx="8" cy="8" r="6.3" fill="none" stroke="#fff" stroke-width="1.4"/><path d="M1.7 8h12.6M8 1.7c-3 3.5-3 9 0 12.6M8 1.7c3 3.5 3 9 0 12.6" fill="none" stroke="#fff" stroke-width="1.2"/></svg>
      </span>
      <span class="rule"></span>
    </div>

    <p class="contact">555.014.2276<br>marisol@velmora.ca<br>www.velmora.ca</p>
    <div class="divider"></div>
    <p class="locations">Northgate NT<span class="dot">•</span>Riverbend NB</p>
  </section>

  <section class="card card-back" aria-label="Card back">
    <div class="back-pattern" role="img" aria-label="Faint spot UV repeating brand pattern on black"></div>
    <div class="back-content">
      <div class="back-brand">
        <span class="brand-name">Velmora</span>
        <span class="brand-mark"></span>
      </div>
      <div class="back-brand-sub">CONSULTING</div>

      <p class="mission">Execution<br>As the owner's rep<br>We aim to achieve your<br>Infrastructure vision <span style="text-transform:none">with</span><br>Our specialization &amp; execution <span style="text-transform:none">in:</span></p>
      <p class="services">FUNDING Planning<br>BUSINESS Planning<br>INFRASTRUCTURE Planning<br>PROJECT Management</p>
      <p class="since">Since 2012</p>
    </div>
  </section>

</main>
</body>
</html>
```